Brackwell Yard Services Flyer Design

I need a new flyer design for my business, Brackwell Yard Services. I’ll be providing my old flyer and logo as references. The new flyer should feature updated wording, contact information, logos, and photos, but still keep the original “What We Do” section and include the phrase “Don’t See? Just Ask!” somewhere near the services. The flyer needs to look great in black and white for door-to-door handouts but also be eye-catching and professional enough for social media use.

The updated content should include the headline “Transforming Outdoor Spaces with Hard Work & Precision” and highlight three main service areas: Landscaping Services (project-based landscaping to clean, prepare, and transform outdoor spaces with precision), Property Cleanup (quick hauls, debris removal, or full cleanouts—no job too big or small), and Ground Preparation (pad preparation, brush removal, and fire lines—making properties safe, functional, and project-ready).

Please also include a “Why Choose Us?” section that lists: Locally owned since 2022, Reliable & affordable – no corners cut, Professional results you can trust, LICENSED AND Insured, and Quality work / on time / references / flexible / follow-up.

At the bottom, include the contact details: Call or Text Today!
www.brackwellyard.example
| sales@brackwellyard.example
| (555) 014-7293

The overall design should be clean, professional, and easy to read with a layout that clearly shows what we offer. Use visuals that represent outdoor services, landscaping, and property cleanup/prep work. I want something that feels trustworthy, family-friendly, and modern.
Use the same photo of leaf clean up from the original flyer if possible.
Our company colors are also black and white. For the most part.

```html
<!DOCTYPE html>
<html lang="en">
<head>
<meta charset="utf-8">
<title>Brackwell Yard Services Flyer</title>
<link rel="stylesheet" href="https://fonts.googleapis.com/css2?family=Bebas+Neue&family=Fira+Sans+Condensed:wght@600&family=Source+Sans+3:wght@400;600;700&display=swap">
<style>
  :root {
    --orange: #f7941d;
    --black: #0b0b0b;
    --white: #ffffff;
    --ink: #1a1a1a;
    --canvas: #ffffff;
  }
  * { box-sizing: border-box; margin: 0; padding: 0; }
  html, body { width: 1200px; height: 765px; overflow: hidden; background: var(--canvas); }
  .sheet { position: relative; width: 1200px; height: 765px; }

  .flyer {
    position: absolute; top: 0; width: 593px; height: 765px;
    background: var(--white); overflow: hidden;
    font-family: "Source Sans 3", sans-serif; color: var(--ink);
  }
  .flyer--color { left: 0; --accent: var(--orange); --band: var(--orange); --footer-accent: var(--orange); }
  .flyer--mono  { left: 607px; --accent: var(--black); --band: var(--black); --footer-accent: var(--white); }

  .header { position: absolute; left: 0; top: 0; width: 100%; height: 63px; background: var(--band); }
  .headline {
    position: absolute; left: 12px; top: 9px; width: 310px; text-align: center;
    font-family: "Bebas Neue", sans-serif; font-size: 24px; line-height: 22px;
    color: var(--white); letter-spacing: 0.3px;
  }
  .brand { position: absolute; right: 14px; top: 12px; display: flex; align-items: center; gap: 7px; }
  .brand-square { width: 26px; height: 26px; background: var(--white); }
  .brand-name {
    font-family: "Bebas Neue", sans-serif; font-size: 18px; line-height: 17px;
    color: var(--white); letter-spacing: 0.5px;
  }

  .photo { position: absolute; top: 66px; height: 197px; width: 194px; }
  .photo--brush  { left: 2px; }
  .photo--leaves { left: 199px; }
  .photo--saw    { left: 396px; width: 195px; }
  .flyer--color .photo--brush  { background: linear-gradient(160deg, #5d6a55 0%, #6f6a5e 45%, #8a7a62 100%); }
  .flyer--color .photo--leaves { background: linear-gradient(170deg, #5f6a4e 0%, #6d6b50 40%, #b08555 75%, #c79a64 100%); }
  .flyer--color .photo--saw    { background: linear-gradient(160deg, #6a6a60 0%, #4e5440 45%, #8a7560 100%); }
  .flyer--mono .photo--brush  { background: linear-gradient(160deg, #4a4a4a 0%, #6a6a6a 50%, #8c8c8c 100%); }
  .flyer--mono .photo--leaves { background: linear-gradient(170deg, #6a6a6a 0%, #7d7d7d 45%, #a9a9a9 100%); }
  .flyer--mono .photo--saw    { background: linear-gradient(160deg, #777 0%, #4d4d4d 45%, #8f8f8f 100%); }

  .tag {
    position: absolute; height: 33px; background: var(--accent);
    font-family: "Fira Sans Condensed", sans-serif; font-weight: 600;
    font-size: 22px; line-height: 33px; color: var(--white); padding-left: 8px;
  }
  .tag--services { left: 23px; top: 275px; width: 130px; }
  .tag--what     { left: 389px; top: 275px; width: 130px; }
  .tag--why      { left: 23px; top: 549px; width: 175px; padding-left: 10px; }

  .service-title, .group-title, .closing {
    position: absolute; font-family: "Bebas Neue", sans-serif; color: var(--accent);
    font-size: 21px; line-height: 20px; letter-spacing: 0.2px;
  }
  .service-body { position: absolute; left: 27px; width: 300px; font-size: 11.2px; line-height: 14px; }

  .divider { position: absolute; left: 354px; top: 290px; width: 1px; height: 395px; background: var(--accent); }

  .list { position: absolute; list-style: none; font-size: 11.2px; }
  .list li { position: relative; height: 19.5px; line-height: 14px; padding-left: 16px; }
  .list li::before {
    content: ""; position: absolute; left: 0; top: 2px; width: 10px; height: 10px; background: var(--accent);
    clip-path: polygon(30% 0, 70% 0, 100% 30%, 100% 70%, 70% 100%, 30% 100%, 0 70%, 0 30%);
  }

  .closing--licensed { left: 0; width: 354px; text-align: center; top: 672px; font-size: 19px; }
  .pillars { position: absolute; left: 0; width: 354px; top: 692px; text-align: center; font-size: 11px; }
  .pillars .dot { color: var(--accent); }
  .closing--ask { left: 390px; top: 672px; font-size: 19px; }

  .footer { position: absolute; left: 0; top: 712px; width: 100%; height: 53px; background: var(--black); }
  .footer-title {
    position: absolute; left: 0; width: 100%; top: 5px; text-align: center;
    font-family: "Bebas Neue", sans-serif; font-size: 22px; line-height: 22px; color: var(--footer-accent);
  }
  .contacts {
    position: absolute; left: 0; width: 100%; top: 30px; display: flex; justify-content: center; gap: 16px;
    font-size: 13px; font-weight: 700; color: var(--footer-accent); line-height: 16px;
  }
  .contact { display: flex; align-items: center; gap: 5px; }
  .contact svg { width: 13px; height: 13px; fill: none; stroke: var(--footer-accent); stroke-width: 1.4; }
</style>
</head>
<body>
<div class="sheet">

  <!-- Colour edition -->
  <section class="flyer flyer--color">
    <header class="header">
      <h1 class="headline">Transforming Outdoor Spaces<br>With Hard Work &amp; Precision</h1>
      <div class="brand"><span class="brand-square"></span><span class="brand-name">Brackwell<br>Yard Services</span></div>
    </header>
    <div class="photo photo--brush" role="img" aria-label="Worker pushing a wheelbarrow loaded with cut branches along a yard path"></div>
    <div class="photo photo--leaves" role="img" aria-label="Worker raking a pile of dry autumn leaves on a lawn"></div>
    <div class="photo photo--saw" role="img" aria-label="Worker in hard hat cutting a fallen tree with a chainsaw"></div>

    <div class="tag tag--services">Our Services</div>
    <h2 class="service-title" style="left:26px;top:320px">Landscaping Services</h2>
    <p class="service-body" style="top:350px">Project-based landscaping to clean, prepare, and transform outdoor spaces with precision.</p>
    <h2 class="service-title" style="left:26px;top:395px">Ground Preparation</h2>
    <p class="service-body" style="top:425px">Pad preparation, brush removal, and fire lines—making properties safe, functional, and project-ready.</p>
    <h2 class="service-title" style="left:26px;top:470px">Property Cleanup</h2>
    <p class="service-body" style="top:500px">Quick hauls, debris removal, or full cleanouts—no job too big or small.</p>

    <div class="tag tag--why">Why Choose Us?</div>
    <ul class="list" style="left:26px;top:592px">
      <li>Locally owned since 2022</li>
      <li>Reliable &amp; affordable – no corners cut</li>
      <li>Professional results you can trust</li>
    </ul>
    <h3 class="closing closing--licensed">Licensed and Insured</h3>
    <p class="pillars">Quality work <span class="dot">•</span> On Time <span class="dot">•</span> References <span class="dot">•</span> Flexible <span class="dot">•</span> Follow-up</p>

    <div class="divider"></div>

    <div class="tag tag--what">What We Do</div>
    <h2 class="group-title" style="left:391px;top:320px">Remove</h2>
    <ul class="list" style="left:393px;top:351px">
      <li>Junk removal</li><li>Trash &amp; waste hauling</li><li>Yard &amp; garden cleanup</li><li>Appliance removal</li>
    </ul>
    <h2 class="group-title" style="left:390px;top:438px">Install</h2>
    <ul class="list" style="left:391px;top:469px">
      <li>Mulch</li><li>DG</li><li>Plants</li><li>Rock</li>
    </ul>
    <h2 class="group-title" style="left:390px;top:557px">Maintenance &amp; Other</h2>
    <ul class="list" style="left:391px;top:588px">
      <li>Yard cleanup</li><li>Weed prevention (pre-emergent)</li><li>Roof &amp; gutter cleaning</li><li>Fence &amp; deck staining</li>
    </ul>
    <h3 class="closing closing--ask">Don’t See? Just Ask!</h3>

    <footer class="footer">
      <p class="footer-title">Call or Text Today!</p>
      <div class="contacts">
        <span class="contact"><svg viewBox="0 0 14 14"><circle cx="7" cy="7" r="6"/><ellipse cx="7" cy="7" rx="2.6" ry="6"/><path d="M1 7h12M2 4h10M2 10h10"/></svg>www.brackwellyard.example</span>
        <span class="contact"><svg viewBox="0 0 14 14"><rect x="1" y="3" width="12" height="8"/><path d="M1 3l6 5 6-5"/></svg>sales@brackwellyard.example</span>
        <span class="contact"><svg viewBox="0 0 14 14"><path d="M3 1.5l2.5 3-1.5 1.5c.8 1.8 2.2 3.2 4 4l1.5-1.5 3 2.5-1.5 2C6 12.5 1.5 8 1 3z"/></svg>(555) 014-7293</span>
      </div>
    </footer>
  </section>

  <!-- Black and white edition -->
  <section class="flyer flyer--mono">
    <header class="header">
      <h1 class="headline">Transforming Outdoor Spaces<br>With Hard Work &amp; Precision</h1>
      <div class="brand"><span class="brand-square"></span><span class="brand-name">Brackwell<br>Yard Services</span></div>
    </header>
    <div class="photo photo--brush" role="img" aria-label="Black and white photo of worker pushing a wheelbarrow of cut branches"></div>
    <div class="photo photo--leaves" role="img" aria-label="Black and white photo of worker raking a pile of leaves"></div>
    <div class="photo photo--saw" role="img" aria-label="Black and white photo of worker cutting a fallen tree with a chainsaw"></div>

    <div class="tag tag--services">Our Services</div>
    <h2 class="service-title" style="left:26px;top:320px">Landscaping Services</h2>
    <p class="service-body" style="top:350px">Project-based landscaping to clean, prepare, and transform outdoor spaces with precision.</p>
    <h2 class="service-title" style="left:26px;top:395px">Ground Preparation</h2>
    <p class="service-body" style="top:425px">Pad preparation, brush removal, and fire lines—making properties safe, functional, and project-ready.</p>
    <h2 class="service-title" style="left:26px;top:470px">Property Cleanup</h2>
    <p class="service-body" style="top:500px">Quick hauls, debris removal, or full cleanouts—no job too big or small.</p>

    <div class="tag tag--why">Why Choose Us?</div>
    <ul class="list" style="left:26px;top:592px">
      <li>Locally owned since 2022</li>
      <li>Reliable &amp; affordable – no corners cut</li>
      <li>Professional results you can trust</li>
    </ul>
    <h3 class="closing closing--licensed">Licensed and Insured</h3>
    <p class="pillars">Quality work <span class="dot">•</span> On Time <span class="dot">•</span> References <span class="dot">•</span> Flexible <span class="dot">•</span> Follow-up</p>

    <div class="divider"></div>

    <div class="tag tag--what">What We Do</div>
    <h2 class="group-title" style="left:391px;top:320px">Remove</h2>
    <ul class="list" style="left:393px;top:351px">
      <li>Junk removal</li><li>Trash &amp; waste hauling</li><li>Yard &amp; garden cleanup</li><li>Appliance removal</li>
    </ul>
    <h2 class="group-title" style="left:390px;top:438px">Install</h2>
    <ul class="list" style="left:391px;top:469px">
      <li>Mulch</li><li>DG</li><li>Plants</li><li>Rock</li>
    </ul>
    <h2 class="group-title" style="left:390px;top:557px">Maintenance &amp; Other</h2>
    <ul class="list" style="left:391px;top:588px">
      <li>Yard cleanup</li><li>Weed prevention (pre-emergent)</li><li>Roof &amp; gutter cleaning</li><li>Fence &amp; deck staining</li>
    </ul>
    <h3 class="closing closing--ask">Don’t See? Just Ask!</h3>

    <footer class="footer">
      <p class="footer-title">Call or Text Today!</p>
      <div class="contacts">
        <span class="contact"><svg viewBox="0 0 14 14"><circle cx="7" cy="7" r="6"/><ellipse cx="7" cy="7" rx="2.6" ry="6"/><path d="M1 7h12M2 4h10M2 10h10"/></svg>www.brackwellyard.example</span>
        <span class="contact"><svg viewBox="0 0 14 14"><rect x="1" y="3" width="12" height="8"/><path d="M1 3l6 5 6-5"/></svg>sales@brackwellyard.example</span>
        <span class="contact"><svg viewBox="0 0 14 14"><path d="M3 1.5l2.5 3-1.5 1.5c.8 1.8 2.2 3.2 4 4l1.5-1.5 3 2.5-1.5 2C6 12.5 1.5 8 1 3z"/></svg>(555) 014-7293</span>
      </div>
    </footer>
  </section>

</div>
</body>
</html>
```